New Webpage for High Class Expert Witness Services Company

We are looking for a minimalist design for a webpage that just has our logo and an entry form offer to connect with one of our Liaisons.
The entry form should just ask for Name, Email, Contact Info and Description of Project.

Company Name is: The Marlowe Crest Advisory Services

Number of Pages Required

1 page

```html
<!DOCTYPE html>
<html lang="en">
<head>
<meta charset="utf-8">
<title>Marlowe Crest Advisory Services</title>
<link href="https://fonts.googleapis.com/css2?family=Cinzel:wght@400;600&family=Manrope:wght@400&family=Roboto:wght@400&display=swap" rel="stylesheet">
<style>
  :root {
    --bg-dark: #1a1a1a;
    --bg-mid: #3a3a3a;
    --text-white: #ffffff;
    --text-soft: #cfcfcf;
    --text-muted: #9a9a9a;
    --line: #8a8a8a;
    --panel-line: #6a6a6a;
    --button-light: #dcdcdc;
    --button-dark: #a5a5a5;
    --button-text: #111111;
  }
  * { box-sizing: border-box; margin: 0; padding: 0; }
  html, body { width: 1200px; height: 742px; overflow: hidden; background: var(--bg-dark); }
  .page { position: relative; width: 1200px; height: 742px; overflow: hidden; }
  .hero-photo {
    position: absolute; inset: 0;
    background:
      radial-gradient(ellipse 520px 420px at 760px 300px, rgba(110,110,110,0.35), transparent 70%),
      radial-gradient(ellipse 420px 520px at 1080px 420px, rgba(120,120,120,0.3), transparent 70%),
      linear-gradient(100deg, #181818 0%, #222 45%, #3d3d3d 75%, #4a4a4a 100%);
  }
  .brand {
    position: absolute; left: 114px; top: 40px;
    display: flex; align-items: center; gap: 14px;
  }
  .brand-mark { width: 40px; height: 40px; background: var(--text-soft); }
  .brand-name {
    font-family: 'Cinzel', serif; font-weight: 400; color: var(--text-soft);
    font-size: 22px; line-height: 26px; letter-spacing: 1px;
  }
  .eyebrow {
    position: absolute; left: 111px; top: 219px;
    font-family: 'Cinzel', serif; font-size: 15px; letter-spacing: 1.6px; color: var(--text-muted);
  }
  .headline-wrap {
    position: absolute; left: 114px; top: 260px; height: 148px;
    border-left: 1px solid var(--line); padding-left: 21px;
  }
  .headline {
    font-family: 'Cinzel', serif; font-weight: 400; color: var(--text-white);
    font-size: 52px; line-height: 51px; letter-spacing: 2px; margin-top: -4px;
  }
  .intro {
    position: absolute; left: 114px; top: 425px; width: 480px;
    font-family: 'Manrope', sans-serif; font-size: 14px; line-height: 28px; color: var(--text-soft);
  }
  .connect-panel {
    position: absolute; left: 715px; top: 124px; width: 378px; height: 437px;
    border: 1px solid var(--panel-line); background: rgba(20,20,20,0.35);
  }
  .connect-title {
    position: absolute; left: 46px; top: 36px;
    font-family: 'Cinzel', serif; font-size: 24px; color: var(--text-white); letter-spacing: 0.5px;
  }
  .field {
    position: absolute; left: 46px; width: 294px; height: 42px;
    border: 1px solid var(--line); background: transparent;
    font-family: 'Roboto', sans-serif; font-size: 13px; color: var(--text-white);
    padding: 0 17px; display: flex; align-items: center;
  }
  .field-message { height: 88px; align-items: flex-start; padding-top: 11px; }
  .submit-button {
    position: absolute; left: 46px; top: 354px; width: 297px; height: 44px;
    background: linear-gradient(110deg, var(--button-light) 0%, #d4d4d4 45%, var(--button-dark) 75%, #b5b5b5 100%);
    border: 0; font-family: 'Cinzel', serif; font-weight: 600; font-size: 15px;
    letter-spacing: 0.5px; color: var(--button-text);
    display: flex; align-items: center; justify-content: center;
  }
  .site-footer {
    position: absolute; left: 0; top: 680px; width: 1200px; height: 62px;
    border-top: 1px solid #444; background: rgba(40,40,40,0.4);
    display: flex; align-items: center; justify-content: center;
    font-family: 'Roboto', sans-serif; font-size: 12.5px; color: var(--text-muted);
  }
</style>
</head>
<body>
<main class="page">
  <div class="hero-photo" role="img" aria-label="Black and white photo of a doctor holding a stethoscope"></div>

  <header class="brand">
    <span class="brand-mark"></span>
    <span class="brand-name">Marlowe Crest<br>Advisory Services</span>
  </header>

  <p class="eyebrow">MARLOWE CREST ADVISORY SERVICES</p>
  <div class="headline-wrap">
    <h1 class="headline">SEAMLESS<br>MEDICAL EXPERT<br>INTEGRATION</h1>
  </div>
  <p class="intro">Lorem ipsum dolor sit amet, consectetur adipiscing elit, sed do eiusmod tempor incididunt ut labore et dolore magna aliqua.</p>

  <section class="connect-panel">
    <h2 class="connect-title">CONNECT WITH US</h2>
    <div class="field" style="top:85px; left:47px;">Name*</div>
    <div class="field" style="top:143px;">Email*</div>
    <div class="field" style="top:197px; left:45px;">Phone number*</div>
    <div class="field field-message" style="top:254px; left:45px;">Description of Project</div>
    <div class="submit-button" style="left:45px;">SUBMIT</div>
  </section>

  <footer class="site-footer">© 2026 Marlowe Crest Advisory Services. All Rights Reserved</footer>
</main>
</body>
</html>
```